Phuket Thailand - Rental Villa Website

I have a villa for rent in Thailand and require a website - i need to demo pictures/walk through video, local attractions, villa facilities description plus seaonal rates and online booking.

Industry/Entity Type

Rental

Coding

Coded - Design and coding required

```html
<!DOCTYPE html>
<html lang="en">
<head>
<meta charset="utf-8">
<title>Villa Rental</title>
<link href="https://fonts.googleapis.com/css2?family=Open+Sans:wght@400;600;700&display=swap" rel="stylesheet">
<style>
:root{
  --teal:#3a9b98;
  --teal-dark:#2f827f;
  --ink:#1f1f1f;
  --bar:#262626;
  --text:#555;
  --paper:#ffffff;
  --field:#ffffff;
  --muted:#9a9a9a;
}
*{box-sizing:border-box;margin:0;padding:0}
html,body{width:791px;height:1200px;overflow:hidden;background:var(--paper);font-family:"Open Sans",Arial,sans-serif;color:var(--text)}
.page{position:relative;width:791px;height:1200px;overflow:hidden}
.topbar{position:absolute;left:0;top:0;width:791px;height:44px;background:var(--ink);border-bottom:3px solid var(--teal)}
.brand{position:absolute;left:40px;top:12px;color:#fff;font-weight:600;font-size:17px;letter-spacing:1px}
.nav{position:absolute;right:40px;top:14px;display:flex;gap:22px;list-style:none}
.nav li{color:#eee;font-size:10px}
.utility{position:absolute;left:0;top:44px;width:791px;height:16px;background:#fff}
.util-btn{position:absolute;right:95px;top:2px;background:var(--ink);color:#fff;font-size:7px;font-weight:700;padding:2px 8px}
.util-fav{position:absolute;right:40px;top:2px;border:1px solid #ccc;font-size:7px;padding:1px 8px;color:#333}
.hero{position:absolute;left:40px;top:60px;width:711px;height:364px;background:linear-gradient(170deg,#cfe3ef 0%,#f4f5f2 30%,#e9ece8 50%,#47707a 70%,#2a5a86 100%)}
.search{position:absolute;left:40px;top:60px;width:711px;height:30px;background:rgba(58,155,152,.9);display:flex;gap:8px;padding:5px 6px}
.field{background:var(--field);height:20px;font-size:8px;color:var(--muted);padding:4px 6px;position:relative}
.field .ic{position:absolute;right:4px;top:5px;width:10px;height:10px;background:#666;border-radius:2px}
.f-name{width:180px}.f-mail{width:180px}.f-date{width:95px}
.search .go{margin-left:auto;background:var(--teal-dark);color:#fff;font-size:8px;font-weight:700;padding:4px 12px;border:1px solid #fff}
.dots{position:absolute;left:0;right:0;top:405px;display:flex;justify-content:center;gap:6px}
.dots span{width:6px;height:6px;border-radius:50%;background:#fff;opacity:.6}
.dots span:first-child{opacity:1}
.section-title{position:absolute;left:40px;color:var(--teal);font-size:12px;font-weight:700;letter-spacing:.5px}
.cards{position:absolute;left:40px;top:477px;width:711px;display:flex;gap:8px}
.card{width:172px;height:224px;box-shadow:0 1px 3px rgba(0,0,0,.25)}
.card .photo{height:120px}
.card .cap{height:68px;background:var(--teal);color:#fff;padding:8px 8px}
.card h3{font-size:9px;font-weight:700;margin-bottom:5px}
.card p{font-size:6.5px;line-height:1.35;opacity:.9}
.card .foot{height:36px;display:flex;justify-content:space-between;align-items:center;padding:0 8px;background:#fff}
.price{color:var(--teal);font-size:10px;font-weight:700}
.more{color:var(--teal);font-size:7px;font-weight:600}
.about{position:absolute;left:40px;top:745px;width:370px}
.about p{font-size:8px;line-height:1.6;margin-bottom:10px}
.learn{position:absolute;left:40px;top:886px;border:1px solid var(--teal);color:var(--teal);font-size:7px;padding:3px 8px}
.video{position:absolute;left:428px;top:727px;width:292px;height:170px}
.video .frame{height:150px;background:linear-gradient(160deg,#6d8aa0 0%,#a58a63 45%,#e7d3b3 75%,#8b6c4f 100%)}
.controls{height:20px;background:#222;position:relative}
.controls .prog{position:absolute;left:28px;top:8px;width:170px;height:4px;background:#555}
.controls .prog i{display:block;width:60px;height:4px;background:#d33}
.controls .play{position:absolute;left:8px;top:6px;width:0;height:0;border-left:8px solid #fff;border-top:4px solid transparent;border-bottom:4px solid transparent}
.controls .time{position:absolute;left:206px;top:5px;color:#ccc;font-size:7px}
.band{position:absolute;left:0;top:940px;width:791px;height:190px;background:var(--teal)}
.band .section-title{color:#fff;top:18px}
.attractions{position:absolute;left:40px;top:45px;width:711px;display:flex;gap:9px}
.attractions div{width:171px;height:127px;border:2px solid rgba(255,255,255,.5)}
.footer{position:absolute;left:0;top:1130px;width:791px;height:70px;background:var(--bar)}
.social{position:absolute;left:0;right:0;top:20px;display:flex;justify-content:center;gap:4px}
.social span{width:12px;height:12px;background:#ddd}
.copy{position:absolute;left:0;right:0;top:40px;text-align:center;color:#bbb;font-size:7px}
.totop{position:absolute;right:24px;top:38px;color:#bbb;font-size:7px}
</style>
</head>
<body>
<div class="page">
  <header class="topbar">
    <div class="brand">VILLA RENTAL</div>
    <ul class="nav"><li>Home</li><li>About us</li><li>local attractions</li><li>villa description</li><li>contact us</li></ul>
  </header>
  <div class="utility"><span class="util-btn">SUBMIT</span><span class="util-fav">Favorites</span></div>

  <div class="hero" role="img" aria-label="Photo of a white villa with palm trees and a blue swimming pool"></div>
  <form class="search">
    <div class="field f-name">Name<span class="ic"></span></div>
    <div class="field f-mail">Email<span class="ic"></span></div>
    <div class="field f-date">Check in<span class="ic"></span></div>
    <div class="field f-date">Check out<span class="ic"></span></div>
    <div class="go">SUBMIT</div>
  </form>
  <div class="dots"><span></span><span></span><span></span><span></span></div>

  <h2 class="section-title" style="top:455px">VILLA FACILITIES</h2>
  <div class="cards">
    <article class="card"><div class="photo" role="img" aria-label="Villa terrace with sea view" style="background:linear-gradient(180deg,#9fb3b8,#5d6b5e)"></div>
      <div class="cap"><h3>Voluptas Sit Aspernatur</h3><p>Totam rem aperiam eaque ipsa quae ab illo inventore veritatis quasi architecto.</p></div>
      <div class="foot"><span class="price">$ 3,40,000</span><span class="more">READ MORE ›</span></div></article>
    <article class="card"><div class="photo" role="img" aria-label="Poolside deck with loungers" style="background:linear-gradient(180deg,#b9a48c,#6f9aa2)"></div>
      <div class="cap"><h3>Voluptas Sit Aspernatur</h3><p>Nemo enim ipsam voluptatem quia voluptas sit aspernatur aut odit fugit sed.</p></div>
      <div class="foot"><span class="price">$ 3,40,000</span><span class="more">READ MORE ›</span></div></article>
    <article class="card"><div class="photo" role="img" aria-label="Infinity pool overlooking the bay" style="background:linear-gradient(180deg,#8fb4c9,#4a8a7e)"></div>
      <div class="cap"><h3>Voluptas Sit Aspernatur</h3><p>Neque porro quisquam est qui dolorem ipsum quia dolor sit amet consectetur.</p></div>
      <div class="foot"><span class="price">$ 3,40,000</span><span class="more">READ MORE ›</span></div></article>
    <article class="card"><div class="photo" role="img" aria-label="Villa rooftop and garden" style="background:linear-gradient(180deg,#a9b9c2,#8b6f5c)"></div>
      <div class="cap"><h3>Voluptas Sit Aspernatur</h3><p>Ut enim ad minima veniam quis nostrum exercitationem ullam corporis suscipit.</p></div>
      <div class="foot"><span class="price">$ 3,40,000</span><span class="more">READ MORE ›</span></div></article>
  </div>

  <h2 class="section-title" style="top:727px">ABOUT US</h2>
  <div class="about">
    <p>Sed ut perspiciatis unde omnis iste natus error sit voluptatem accusantium doloremque laudantium, totam rem aperiam, eaque ipsa quae ab illo inventore veritatis et quasi architecto beatae vitae dicta sunt explicabo. Nemo enim ipsam voluptatem quia voluptas sit aspernatur aut odit aut fugit, sed quia consequuntur magni dolores eos qui ratione.</p>
    <p>Ut enim ad minima veniam, quis nostrum exercitationem ullam corporis suscipit laboriosam, nisi ut aliquid ex ea commodi consequatur. Quis autem vel eum iure reprehenderit qui in ea voluptate velit esse quam nihil molestiae consequatur, vel illum qui dolorem.</p>
  </div>
  <span class="learn">LEARN MORE</span>
  <div class="video">
    <div class="frame" role="img" aria-label="Walk-through video of the villa interior and veranda"></div>
    <div class="controls"><span class="play"></span><span class="prog"><i></i></span><span class="time">0:42 / 3:15</span></div>
  </div>

  <section class="band">
    <h2 class="section-title">LOCAL ATTRACTIONS</h2>
    <div class="attractions">
      <div role="img" aria-label="Golden temple at dusk" style="background:linear-gradient(180deg,#5a4a8c,#c27a3a)"></div>
      <div role="img" aria-label="Temple reflected in a lake" style="background:linear-gradient(180deg,#8fb6d6,#b58a44)"></div>
      <div role="img" aria-label="Tropical beach with palms" style="background:linear-gradient(180deg,#3f8fd0,#9fd6d8 60%,#e8dcc0)"></div>
      <div role="img" aria-label="Resort pavilion by a pool" style="background:linear-gradient(180deg,#2f4f7a,#b5713a 60%,#3e7fa6)"></div>
    </div>
  </section>

  <footer class="footer">
    <div class="social"><span></span><span></span><span></span><span></span><span></span><span></span></div>
    <div class="copy">Copyright © 2015 villa rental, All rights reserved</div>
    <div class="totop">▲ TOP</div>
  </footer>
</div>
</body>
</html>
```